Bramblewood Card Company Business Cards

We are a trading card store with Glimmorax, sports and other TCG cards, we need a business card design that encompasses a clean cut, modern style with a retro flare. website is bramblewoodcardco.com for reference. Can utilize a comic book era feel or a more modern outdoor feel to utilize the "Pacific Northwest" elements of tress, mountains, etc.

Industry/Entity Type

Trading cards and collectibles

Contact Information for Business Card

business name, email address, phone number, name, owner job title

Font styles to use
Sans Serif

```html
<!DOCTYPE html>
<html lang="en">
<head>
<meta charset="utf-8">
<title>Bramblewood Card Company – Business Cards</title>
<link href="https://fonts.googleapis.com/css2?family=Montserrat:wght@400;500;700&display=swap" rel="stylesheet">
<style>
  :root {
    --backdrop: #d3d6d7;
    --card: #f7f7f6;
    --ink: #2b2b2b;
    --slate: #3c3d3e;
    --teal: #1a9cc4;
    --rule: #8a8a8a;
  }
  * { box-sizing: border-box; margin: 0; padding: 0; }
  html, body {
    width: 1200px; height: 829px; overflow: hidden;
    background: var(--backdrop);
    font-family: "Montserrat", sans-serif;
    color: var(--ink);
  }
  .stage {
    width: 1200px; height: 829px;
    display: flex; align-items: center; justify-content: center; gap: 60px;
  }
  .card {
    position: relative;
    width: 525px; height: 300px;
    background: var(--card);
    border-bottom: 4px solid var(--teal);
    box-shadow: 0 10px 30px rgba(0,0,0,0.15);
  }
  /* front */
  .holder-name {
    position: absolute; left: 40px; top: 44px;
    color: var(--teal); font-weight: 700; font-size: 26px; letter-spacing: 1px;
    line-height: 32px;
  }
  .holder-role {
    position: absolute; left: 40px; top: 78px;
    font-size: 14px; letter-spacing: 0.5px; line-height: 18px;
  }
  .rule-short {
    position: absolute; left: 40px; top: 104px; width: 160px; height: 1px; background: var(--rule);
  }
  .contact-list {
    position: absolute; left: 40px; top: 118px; list-style: none;
    font-size: 13px; line-height: 24px;
  }
  .contact-list li { display: flex; align-items: center; gap: 8px; }
  .contact-list svg { width: 11px; height: 11px; flex: none; }
  .icon-fill { fill: var(--teal); }
  .icon-line { fill: none; stroke: var(--teal); stroke-width: 2.5; stroke-linejoin: round; }
  .rule-long {
    position: absolute; left: 40px; right: 40px; top: 212px; height: 1px; background: var(--rule);
  }
  .address {
    position: absolute; right: 40px; bottom: 26px; text-align: right;
    font-style: normal; font-size: 13px; line-height: 19px; letter-spacing: 0.5px;
  }
  .brand-mark {
    position: absolute; display: flex; align-items: center; gap: 10px;
  }
  .brand-mark .dot { background: var(--teal); border-radius: 50%; flex: none; }
  .brand-mark .brand-name {
    color: var(--slate); font-weight: 700; text-transform: uppercase; line-height: 1.15;
  }
  .card-front .brand-mark { right: 40px; top: 60px; width: 170px; }
  .card-front .dot { width: 14px; height: 14px; }
  .card-front .brand-name { font-size: 15px; }
  /* back */
  .card-back .brand-mark {
    left: 50%; top: 50%; transform: translate(-50%, -50%); width: 280px;
  }
  .card-back .dot { width: 22px; height: 22px; }
  .card-back .brand-name { font-size: 24px; }
</style>
</head>
<body>
<main class="stage">
  <section class="card card-front">
    <h1 class="holder-name">DALEN MARSH</h1>
    <p class="holder-role">CEO/Founder</p>
    <div class="rule-short"></div>
    <ul class="contact-list">
      <li><svg viewBox="0 0 24 24" aria-hidden="true"><path class="icon-fill" d="M6.6 10.8a15 15 0 006.6 6.6l2.2-2.2c.3-.3.7-.4 1-.2 1.1.4 2.3.6 3.6.6.6 0 1 .4 1 1V20c0 .6-.4 1-1 1A17 17 0 013 4c0-.6.4-1 1-1h3.5c.6 0 1 .4 1 1 0 1.3.2 2.5.6 3.6.1.3 0 .7-.2 1z"/></svg>(555) 318 2746</li>
      <li><svg viewBox="0 0 24 24" aria-hidden="true"><rect class="icon-line" x="2" y="5" width="20" height="14"/><path class="icon-line" d="M2 5l10 8 10-8"/></svg>info@bramblewoodcardco.com</li>
      <li><svg viewBox="0 0 24 24" aria-hidden="true"><circle class="icon-line" cx="12" cy="12" r="10"/><path class="icon-line" d="M2 12h20M12 2c3 3 3 17 0 20M12 2c-3 3-3 17 0 20"/></svg>www.bramblewoodcardco.com</li>
    </ul>
    <div class="brand-mark">
      <span class="dot"></span>
      <span class="brand-name">Bramblewood Card Company</span>
    </div>
    <div class="rule-long"></div>
    <address class="address">P.O. Box 7731 Fern Lane<br>Cedar Vale WA 4417</address>
  </section>

  <section class="card card-back">
    <div class="brand-mark">
      <span class="dot"></span>
      <span class="brand-name">Bramblewood Card Company</span>
    </div>
  </section>
</main>
</body>
</html>
```